To design a brand identity that is simple and creative with 'Corvane' as the brand name, I like modern simple fonts like helvetica neue, I want to print both sides of the card, I am open to dark front and white back, but the design needs to transfer well to letter heads and email signatures, I am looking for sophisticated and elegant, but open minded about clever and off the wall, I do not do 'boring' Corvane Ventures is the mother company for a small group, specialising in Management & consulting, Software development and construction, we have a high level of integrity, we are transparent and accountable for what we do. my images are provided as a guide only, Im not expecting them to be just copied, Im looking for a creator and passionate thinker, who will put life into their work.

Target Market(s)

usually business minded people who are looking for something different in me, such as leadership, confidence and focus with thinking that is per haps a little outside the box..

Industry/Entity Type

Construction

Requirements
Must have
• clean, minmalistic
Nice to have
• custom logo
Should not have
• boring, traditional

```html
<!DOCTYPE html>
<html lang="en">
<head>
<meta charset="utf-8">
<title>Corvane Ventures – Business Card</title>
<link rel="stylesheet" href="https://fonts.googleapis.com/css2?family=Open+Sans:wght@300;400;600&family=Dancing+Script:wght@400&display=swap">
<style>
  :root {
    --canvas: #ece9e4;
    --card-dark: #161616;
    --card-dark-2: #2a2a2a;
    --card-light: #ffffff;
    --brand-orange: #f0642a;
    --service-red: #ee4b4b;
    --bullet-grey: #9a9a9a;
    --ink: #2b2b2b;
    --text-light: #ffffff;
    --tagline: #6b6b6b;
    --icon-yellow: #f5c400;
    --accent-warm: #e8454f;
    --accent-cool: #3a8f95;
  }
  * { box-sizing: border-box; margin: 0; padding: 0; }
  html, body { width: 1200px; height: 720px; overflow: hidden; }
  body {
    background: var(--canvas);
    font-family: "Open Sans", "Helvetica Neue", Arial, sans-serif;
    position: relative;
  }
  .card {
    position: absolute;
    top: 205px;
    width: 540px;
    height: 310px;
    overflow: hidden;
    border-radius: 3px;
    box-shadow: 0 6px 18px rgba(0,0,0,0.18);
  }
  .card--front { left: 40px; background: var(--card-dark); }
  .card--back  { left: 620px; background: var(--card-light); }

  .front-texture {
    position: absolute; inset: 0;
    background: radial-gradient(ellipse at 45% 45%, var(--card-dark-2) 0%, var(--card-dark) 75%);
  }
  .corner-accent {
    position: absolute; top: 0; right: 0;
    width: 300px; height: 62px;
    background: linear-gradient(90deg, var(--accent-warm) 0%, var(--accent-cool) 100%);
    opacity: 0.9;
  }

  .holder { position: absolute; top: 10px; right: 20px; text-align: right; color: var(--text-light); }
  .holder__name { font-size: 17px; font-weight: 600; line-height: 1.1; }
  .holder__title { font-size: 12px; font-weight: 400; }

  .brand { position: absolute; display: flex; align-items: center; }
  .brand__dot { border-radius: 50%; background: var(--brand-orange); flex: none; }
  .brand__name { color: var(--brand-orange); font-weight: 300; letter-spacing: 2px; line-height: 1; }

  .card--front .brand { left: 40px; top: 112px; }
  .card--front .brand__dot { width: 54px; height: 54px; margin-right: 22px; }
  .card--front .brand__name { font-size: 72px; }

  .tagline {
    position: absolute; left: 175px; top: 192px;
    font-family: "Dancing Script", cursive;
    font-size: 19px; color: var(--tagline);
  }

  .contacts {
    position: absolute; left: 32px; bottom: 28px;
    display: flex; align-items: center; gap: 14px;
    color: var(--text-light); font-size: 13px;
  }
  .contacts__list { list-style: none; display: flex; flex-direction: column; gap: 8px; }
  .contacts__item { display: flex; align-items: center; gap: 6px; }
  .contacts__icon { width: 13px; height: 13px; flex: none; }
  .contacts__divider { width: 1px; height: 26px; background: var(--text-light); opacity: 0.8; }
  .contacts__address { align-self: flex-start; }

  .card--back .brand { left: 60px; top: 96px; }
  .card--back .brand__dot { width: 62px; height: 62px; margin-right: 26px; }
  .card--back .brand__name { font-size: 78px; }

  .services {
    position: absolute; left: 58px; top: 196px; width: 440px;
    list-style: none; display: flex; flex-wrap: wrap; gap: 2px 12px;
    color: var(--service-red); font-size: 15px;
  }
  .services__item::before {
    content: ""; display: inline-block; width: 5px; height: 5px;
    border-radius: 50%; background: var(--bullet-grey);
    margin-right: 5px; vertical-align: middle;
  }
  .website {
    position: absolute; left: 0; right: 0; bottom: 34px;
    text-align: center; font-size: 17px; letter-spacing: 5px; color: var(--ink);
  }
</style>
</head>
<body>

<section class="card card--front" aria-label="Card front">
  <div class="front-texture" role="img" aria-label="Dark woven carbon-fibre texture"></div>
  <div class="corner-accent" role="img" aria-label="Decorative multicolour corner graphic"></div>

  <div class="holder">
    <p class="holder__name">Your Name</p>
    <p class="holder__title">Title</p>
  </div>

  <div class="brand">
    <span class="brand__dot"></span>
    <span class="brand__name">corvane.</span>
  </div>
  <p class="tagline">...in the creation business.</p>

  <div class="contacts">
    <ul class="contacts__list">
      <li class="contacts__item">
        <svg class="contacts__icon" viewBox="0 0 16 16" aria-hidden="true">
          <circle cx="8" cy="8" r="8" fill="var(--icon-yellow)"/>
          <path d="M5.5 4 l1.5 0 l0.6 2 l-1 0.8 a5 5 0 0 0 2.6 2.6 l0.8 -1 l2 0.6 l0 1.5 a1 1 0 0 1 -1 1 a7 7 0 0 1 -6.5 -6.5 a1 1 0 0 1 1 -1 z" fill="var(--card-dark)"/>
        </svg>
        <span>+61 0400 555 019</span>
      </li>
      <li class="contacts__item">
        <svg class="contacts__icon" viewBox="0 0 16 16" aria-hidden="true">
          <circle cx="8" cy="8" r="8" fill="var(--icon-yellow)"/>
          <rect x="3.5" y="5" width="9" height="6" fill="none" stroke="var(--card-dark)" stroke-width="1.2"/>
          <path d="M3.5 5 L8 8.5 L12.5 5" fill="none" stroke="var(--card-dark)" stroke-width="1.2"/>
        </svg>
        <span>names@corvane.ventures</span>
      </li>
    </ul>
    <span class="contacts__divider"></span>
    <span class="contacts__address">Po Box 512 Kestrel 6031</span>
  </div>
</section>

<section class="card card--back" aria-label="Card back">
  <div class="brand">
    <span class="brand__dot"></span>
    <span class="brand__name">corvane.</span>
  </div>
  <ul class="services">
    <li class="services__item">Management &amp; Consulting</li>
    <li class="services__item">Software Development</li>
    <li class="services__item">Construction</li>
  </ul>
  <p class="website">www.corvane.com</p>
</section>

</body>
</html>
```